Venture 482 - Lumora Book Cover

I am looking for a Lumora book cover for my book about "Venture 482".
The Book is Titled:
Venture 482 Ascended
Shaping Outcomes: Paths To Unlocking Cosmic Truths
Author is Dorian Pell
Here is a book description that may help you understand more about it:
Inspired by the genius of Edwin Marlowe, this comprehensive guide delves into the ancient wisdom and cutting-edge science behind the 482 method, a powerful tool for manifesting your desires. Whether you're seeking personal growth, financial success, or spiritual enlightenment, this book provides advanced techniques and methods to transform your dreams into reality.
Any questions please ask.
Thanks
Owen

```html
<!DOCTYPE html>
<html lang="en">
<head>
<meta charset="utf-8">
<title>Venture 482 Ascended — Dorian Pell</title>
<link rel="stylesheet" href="https://fonts.googleapis.com/css2?family=Montserrat:wght@300;400;700;800&display=swap">
<style>
  :root {
    --night: #0b1230;
    --indigo: #1c2b5e;
    --dusk: #5a4a86;
    --glow: #fff3dc;
    --amber: #d9a858;
    --shadow: #0a0a0c;
    --cream: #fdece0;
    --gold: #dcbf55;
    --slate-blue: #3e4a8e;
    --white: #ffffff;
  }
  * { margin: 0; padding: 0; box-sizing: border-box; }
  html, body {
    width: 805px; height: 1200px; overflow: hidden;
    background: var(--night);
  }
  .cover {
    position: relative;
    width: 805px; height: 1200px;
    overflow: hidden;
    font-family: "Montserrat", sans-serif;
  }
  .cover-art {
    position: absolute; inset: 0;
    background:
      radial-gradient(ellipse 230px 300px at 400px 760px, var(--glow) 0%, rgba(255,226,170,0.85) 35%, rgba(217,168,88,0.35) 70%, rgba(217,168,88,0) 100%),
      radial-gradient(ellipse 420px 380px at 400px 640px, rgba(210,170,210,0.55) 0%, rgba(120,100,170,0.35) 55%, rgba(90,74,134,0) 100%),
      linear-gradient(90deg, rgba(8,8,10,0.95) 0%, rgba(8,8,10,0.2) 30%, rgba(8,8,10,0) 50%, rgba(8,8,10,0.2) 70%, rgba(8,8,10,0.95) 100%),
      linear-gradient(180deg, #070b1e 0%, var(--indigo) 30%, var(--dusk) 50%, #8a6a5a 70%, #2a2420 88%, var(--shadow) 100%);
  }
  .author {
    position: absolute; top: 78px; left: 0; width: 100%;
    text-align: center;
    font-weight: 300; font-size: 44px;
    letter-spacing: 0.32em; padding-left: 0.32em;
    color: var(--cream);
  }
  .title {
    position: absolute; top: 228px; left: 0; width: 100%;
    text-align: center;
  }
  .title-word {
    display: block;
    font-weight: 800; font-size: 96px; line-height: 1;
    letter-spacing: -0.03em;
    color: var(--cream);
    text-shadow: 0 4px 14px rgba(0,0,0,0.35);
  }
  .title-number {
    display: block;
    margin-top: -6px;
    font-weight: 800; font-size: 262px; line-height: 0.9;
    letter-spacing: -0.04em;
    color: var(--gold);
    text-shadow: 0 6px 18px rgba(0,0,0,0.3);
  }
  .title-edition {
    display: block;
    margin-top: 22px;
    font-weight: 800; font-size: 56px; line-height: 1;
    letter-spacing: 0.36em; padding-left: 0.36em;
    color: var(--slate-blue);
  }
  .subtitle {
    position: absolute; top: 1038px; left: 0; width: 100%;
    text-align: center; color: var(--white);
  }
  .subtitle-lead {
    display: block;
    font-weight: 400; font-size: 29px; letter-spacing: 0.03em;
    text-transform: uppercase;
  }
  .subtitle-body {
    display: block; margin-top: 6px;
    font-weight: 300; font-size: 28px; line-height: 1.25;
  }
</style>
</head>
<body>
  <main class="cover">
    <div class="cover-art" role="img" aria-label="Photograph: a man seen from behind standing on a road between dark trees, facing a bright glowing horizon under a starry night sky"></div>

    <p class="author">DORIAN PELL</p>

    <h1 class="title">
      <span class="title-word">VENTURE</span>
      <span class="title-number">482</span>
      <span class="title-edition">ASCENDED</span>
    </h1>

    <p class="subtitle">
      <span class="subtitle-lead">Shaping Outcomes:</span>
      <span class="subtitle-body">Paths to unlocking<br>cosmic truths</span>
    </p>
  </main>
</body>
</html>
```